Corporate Travel Technology Company needs new Business Card design

We need a new business card design to reflect our re-branded company. Our company is called tolvEn (pronounced tolvenn) and we provide Business Intelligence and mobile travel management solutions for the corporate travel industry. Our multinational customers use our solutions to manage large travel budgets and frequent travellers, as well as to save money and reduce risk. We'd like to see designs that use the blue and green palette as well as our corporate logo (attached below). The design should communicate innovation, insight, forward thinking, contemporary, trusted.

Target Market(s)

Large multinational corporates and Travel Agencies.

Industry/Entity Type

Business

Contact Information for Business Card

Rosalind Mercer
Chief Executive
tolvEn
Phone number - +61 (0)2 8134 2907
Email address - rosalind.mercer@tolven-example.com
Mobile number - +61 (0)438 516 702
www.tolven-example.com

Font styles to use
Other font styles liked:
• Please use font as close to corporate logo as possible

Colors
0255a3
0393ce
00a990
33b8a4
33a6d7
3176b5

Requirements
Must have
• Please include the words;
• Mobile Travel Management
• Accelerating Travel Business Insights
• Use corporate logo - although icon can be stylised if needed

```html
<!DOCTYPE html>
<html lang="en">
<head>
<meta charset="utf-8">
<title>tolvEn – Business Card</title>
<link href="https://fonts.googleapis.com/css2?family=Open+Sans:wght@400;600&display=swap" rel="stylesheet">
<style>
  :root {
    --page-bg: #e9ebed;
    --card-white: #ffffff;
    --brand-blue: #2a9fd6;
    --brand-slate: #465a5e;
    --text-dark: #2b2b2b;
    --text-grey: #4a4f52;
    --card-shadow: 0 10px 30px rgba(0,0,0,0.18);
  }
  * { box-sizing: border-box; margin: 0; padding: 0; }
  html, body {
    width: 1200px; height: 902px; overflow: hidden;
    background: var(--page-bg);
    font-family: "Open Sans", sans-serif;
  }
  .sheet {
    width: 1200px; height: 902px;
    display: flex; align-items: center; justify-content: center; gap: 40px;
  }
  .card {
    position: relative;
    width: 560px; height: 320px;
    border-radius: 4px;
    overflow: hidden;
    box-shadow: var(--card-shadow);
  }
  /* Back side */
  .card--back {
    background: var(--brand-blue);
    display: flex; flex-direction: column; align-items: center; justify-content: center;
    gap: 6px;
  }
  .wordmark {
    display: flex; align-items: center; gap: 14px;
    color: var(--brand-slate);
    font-weight: 400;
    letter-spacing: -1px;
    line-height: 1.1;
  }
  .wordmark__dot {
    border-radius: 50%;
    background: var(--card-white);
  }
  .card--back .wordmark { font-size: 104px; }
  .card--back .wordmark__dot { width: 46px; height: 46px; }
  .tagline {
    color: var(--card-white);
    font-size: 14px;
    letter-spacing: 0.5px;
  }

  /* Front side */
  .card--front { background: var(--card-white); }
  .card--front .wordmark {
    position: absolute; top: 38px; right: 34px;
    font-size: 62px;
  }
  .card--front .wordmark__dot {
    width: 26px; height: 26px;
    background: var(--brand-blue);
  }
  .holder {
    position: absolute; left: 36px; top: 96px;
  }
  .holder__name {
    color: var(--brand-blue);
    font-weight: 600;
    font-size: 21px;
    line-height: 28px;
  }
  .holder__title {
    color: var(--text-grey);
    font-size: 15px;
    line-height: 20px;
    margin-top: 2px;
  }
  .contact-list {
    position: absolute; left: 36px; top: 170px;
    list-style: none;
  }
  .contact-list li {
    display: flex; align-items: center; gap: 9px;
    font-size: 13.5px; line-height: 18px;
    color: var(--text-dark);
    margin-bottom: 1px;
  }
  .contact-icon {
    width: 13px; height: 13px; flex: none;
    background: var(--brand-blue);
    display: flex; align-items: center; justify-content: center;
  }
  .contact-icon svg { width: 9px; height: 9px; }
  .wave {
    position: absolute; left: 0; top: 0;
    width: 560px; height: 320px;
  }
  .wave__band { fill: var(--brand-slate); }
  .wave__fill { fill: var(--brand-blue); }
  .card--front .tagline {
    position: absolute; right: 30px; bottom: 20px;
    font-size: 13px;
  }
</style>
</head>
<body>
<main class="sheet">
  <section class="card card--back" aria-label="Card back">
    <div class="wordmark"><span class="wordmark__dot"></span><span>tolvEn</span></div>
    <p class="tagline">Accelerating Travel Business Insights</p>
  </section>

  <section class="card card--front" aria-label="Card front">
    <svg class="wave" viewBox="0 0 560 320" aria-hidden="true">
      <path class="wave__band" d="M0 280 C170 288 255 276 325 232 C395 184 470 150 560 138 L560 150 C474 162 402 194 333 242 C262 288 170 300 0 293 Z"/>
      <path class="wave__fill" d="M0 302 C172 309 268 298 340 252 C410 206 480 172 560 160 L560 320 L0 320 Z"/>
    </svg>

    <div class="wordmark"><span class="wordmark__dot"></span><span>tolvEn</span></div>

    <div class="holder">
      <p class="holder__name">Rosalind Mercer</p>
      <p class="holder__title">Chief Executive</p>
    </div>

    <ul class="contact-list">
      <li><span class="contact-icon"><svg viewBox="0 0 10 10"><rect x="3" y="1" width="4" height="8" rx="0.8" fill="none" stroke="#fff" stroke-width="1"/></svg></span>+61 (0)438 516 702</li>
      <li><span class="contact-icon"><svg viewBox="0 0 10 10"><path d="M2 1 L4 1 L4.6 3.2 L3.4 4 C4 5.4 4.6 6 6 6.6 L6.8 5.4 L9 6 L9 8 C5 8.4 1.6 5 2 1 Z" fill="#fff"/></svg></span>+61 (0)2 8134 2907</li>
      <li><span class="contact-icon"><svg viewBox="0 0 10 10"><rect x="1" y="2.5" width="8" height="5" fill="none" stroke="#fff" stroke-width="1"/><path d="M1 2.5 L5 5.5 L9 2.5" fill="none" stroke="#fff" stroke-width="1"/></svg></span>rosalind.mercer@tolven-example.com</li>
      <li><span class="contact-icon"><svg viewBox="0 0 10 10"><circle cx="5" cy="5" r="3.6" fill="none" stroke="#fff" stroke-width="1"/><path d="M1.4 5 H8.6 M5 1.4 C3 3.5 3 6.5 5 8.6 C7 6.5 7 3.5 5 1.4" fill="none" stroke="#fff" stroke-width="0.8"/></svg></span>www.tolven-example.com</li>
    </ul>

    <p class="tagline">Mobile Travel Management</p>
  </section>
</main>
</body>
</html>
```